13 Varno - new website design project

Our company Varno Electrical is developing a new lead generation website focused on Electrical, LED Lighting and Solar Power. We need a high converting website.

Example of our current website is www.varnoelectrical-example.com.au You can take content from this website for this new design. Our colours are red, black and white. For our new website we would like to promote Varno, Spark Every Day. Please listen to the jingle.

The below link is the company jingle that we have developed.
http://www.tunecraftdemo.com.au/vrn-tc-v1/

The key for this brief is to generate leads for Electrical, LED Lighting (for commercial) and Solar Power & Storage.

Target Market(s)

Business owners in Melbourne Victoria

Number of Pages Required

4 page

Colors
ec1f27
ffffff

Requirements
Must have
• This page must be clean, be in line with company branding and a high converting lead website.

```html
<!DOCTYPE html>
<html lang="en">
<head>
<meta charset="utf-8">
<title>Varno Electrical</title>
<link href="https://fonts.googleapis.com/css2?family=Roboto:wght@400;500;700&family=Open+Sans:wght@400;600;700&display=swap" rel="stylesheet">
<style>
:root{
  --red:#ec1f27;
  --red-dark:#c9151c;
  --ink:#2b2b2b;
  --dark:#222326;
  --nav-active:#2e3036;
  --grey-bg:#f4f5f7;
  --text:#666;
  --white:#fff;
}
*{margin:0;padding:0;box-sizing:border-box}
html,body{width:1200px;height:2594px;overflow:hidden}
body{position:relative;background:var(--white);font-family:"Open Sans",Arial,sans-serif;color:var(--text)}
.abs{position:absolute}

/* header */
.site-header{left:0;top:0;width:1200px;height:107px;background:var(--white)}
.brand{left:86px;top:14px}
.brand-name{font-family:"Roboto",sans-serif;font-weight:700;font-size:46px;line-height:48px;color:var(--ink);letter-spacing:1px}
.brand-tag{font-family:"Roboto",sans-serif;font-size:14px;color:var(--ink);margin-top:2px}
.brand-tag span{color:var(--red)}
.hotline{right:86px;top:22px;display:flex;align-items:center;gap:8px}
.hotline-num{font-family:"Roboto",sans-serif;font-weight:700;font-size:54px;line-height:54px;color:var(--red)}
.hotline-sub{display:flex;flex-direction:column;line-height:1}
.hotline-sub b{font-family:"Roboto",sans-serif;font-size:34px;color:var(--red)}
.hotline-sub i{font-style:normal;font-family:"Roboto",sans-serif;font-weight:700;font-size:15px;color:var(--white);background:var(--ink);letter-spacing:5px;padding:1px 4px;text-align:center}

/* nav */
.main-nav{left:0;top:107px;width:1200px;height:59px;background:var(--red);border-bottom:2px solid var(--red-dark)}
.main-nav ul{list-style:none;display:flex;margin-left:86px;height:100%}
.main-nav li{font-family:"Open Sans",sans-serif;font-weight:600;font-size:12px;color:var(--white);display:flex;align-items:center;justify-content:center;height:100%}
.main-nav li.active{background:var(--nav-active)}

/* hero */
.hero{left:0;top:166px;width:1200px;height:498px}
.hero-photo{position:absolute;inset:0;background:radial-gradient(ellipse at 40% 45%,#e9b77a 0%,#c9683e 25%,#6e2a6a 55%,#2a1f7a 100%)}
.hero-title{position:absolute;left:0;width:100%;top:170px;text-align:center;font-family:"Roboto",sans-serif;font-weight:500;font-size:70px;color:var(--white)}
.hero-sub{position:absolute;left:0;width:100%;top:278px;text-align:center;font-family:"Open Sans",sans-serif;font-weight:700;font-size:15px;color:var(--white)}
.hero-arrow{position:absolute;top:223px;width:52px;height:52px;border:2px solid var(--white);border-radius:50%}
.hero-arrow svg{display:block;margin:14px auto}

/* about */
.about{left:0;top:664px;width:1200px;height:443px;background:var(--grey-bg)}
.section-title{font-family:"Roboto",sans-serif;font-weight:500;font-size:27px;color:var(--ink)}
.section-title em{font-style:normal;color:var(--red)}
.about .section-title{position:absolute;left:86px;top:48px}
.about-text{position:absolute;left:86px;top:102px;width:566px;font-size:11.5px;line-height:26px;color:#555}
.about-text p+p{margin-top:20px}
.btn-red{position:absolute;left:86px;top:328px;width:147px;height:42px;background:var(--red);color:var(--white);border-radius:3px;font-weight:600;font-size:12px;display:flex;align-items:center;justify-content:center}
.about-photo{position:absolute;left:640px;top:54px}

/* services */
.services{left:0;top:1107px;width:1200px;height:446px;background:var(--red)}
.services .section-title{position:absolute;left:0;width:100%;text-align:center;top:52px;color:var(--white)}
.services-intro{position:absolute;left:0;width:100%;text-align:center;top:92px;font-size:12px;color:var(--white)}
.service{position:absolute;top:146px;width:327px}
.service-photo{width:327px;height:225px;border:3px solid #f1f1f1}
.service-name{margin-top:14px;text-align:center;font-family:"Roboto",sans-serif;font-weight:500;font-size:21px;color:var(--white)}

/* why */
.why{left:0;top:1553px;width:1200px;height:415px}
.center-title{position:absolute;left:0;width:100%;text-align:center}
.center-sub{position:absolute;left:0;width:100%;text-align:center;font-size:11.5px;color:#555}
.feature{position:absolute;top:132px;width:240px;text-align:center}
.feature-icon{width:122px;height:122px;margin:0 auto;border-radius:50%;border:3px solid currentColor;padding:5px}
.feature-icon div{width:100%;height:100%;border-radius:50%;background:currentColor;display:flex;align-items:center;justify-content:center}
.feature.red{color:var(--red)}
.feature.dark{color:var(--ink)}
.feature h3{margin-top:20px;font-family:"Open Sans",sans-serif;font-weight:600;font-size:16px}
.feature.dark h3{font-weight:400;color:#333}
.feature p{margin-top:14px;font-size:11.5px;line-height:26px;color:#555}

/* clients */
.clients{left:0;top:1968px;width:1200px;height:280px;background:var(--grey-bg)}
.client{position:absolute;top:128px;width:173px;height:97px;background:var(--white);border:1px solid #e6e6e6;display:flex;align-items:center;justify-content:center;gap:8px;font-family:"Roboto",sans-serif;font-weight:500;font-size:17px;color:#333;white-space:nowrap}
.client i{width:12px;height:12px;background:var(--red);display:block;flex:none}

/* footer */
.site-footer{left:0;top:2248px;width:1200px;height:346px;background:var(--dark);color:var(--white)}
.foot-brand{position:absolute;left:104px;top:62px}
.foot-brand .brand-name{color:var(--white);font-size:62px;line-height:64px}
.foot-brand .brand-tag{color:var(--white);font-size:19px}
.socials{position:absolute;left:104px;top:184px;display:flex;gap:8px}
.socials span{width:34px;height:34px;border:2px solid var(--white);border-radius:50%}
.foot-head{position:absolute;top:40px;font-family:"Roboto",sans-serif;font-weight:500;font-size:18px;color:var(--red)}
.field{position:absolute;border:1px solid #cfcfcf;border-radius:3px;font-size:10px;color:var(--white);padding:9px 9px}
.submit{position:absolute;left:382px;top:200px;width:90px;height:31px;border:1px solid #cfcfcf;border-radius:3px;font-weight:700;font-size:12px;display:flex;align-items:center;justify-content:center}
.contact-block{position:absolute;left:720px;top:80px;font-size:11px;line-height:22px}
.contact-row{display:flex;align-items:center;gap:10px;margin-top:14px;white-space:nowrap}
.contact-row.email span{font-size:10px}
.quick-links{position:absolute;left:998px;top:82px;list-style:none;font-size:11.5px;line-height:25px}
.quick-links li::before{content:"»";margin-right:22px}
.foot-rule{position:absolute;left:86px;top:276px;width:1028px;height:1px;background:#3a3b3e}
.copyright{position:absolute;left:0;width:100%;top:300px;text-align:center;font-size:11px}
</style>
</head>
<body>

<header class="site-header abs">
  <div class="brand abs">
    <div class="brand-name">VARNO</div>
    <div class="brand-tag">Spark <span>Every</span> Day</div>
  </div>
  <div class="hotline abs">
    <svg width="62" height="50" viewBox="0 0 62 50" aria-hidden="true">
      <path d="M4 20 Q31 0 58 20 L54 28 L44 24 L42 16 Q31 12 20 16 L18 24 L8 28 Z" fill="#2b2b2b"/>
      <rect x="12" y="26" width="38" height="22" rx="5" fill="#2b2b2b"/>
      <circle cx="31" cy="37" r="6" fill="#fff"/>
    </svg>
    <div class="hotline-num">13</div>
    <div class="hotline-sub"><b>7261</b><i>VARNO</i></div>
  </div>
</header>

<nav class="main-nav abs">
  <ul>
    <li class="active" style="width:125px">HOME</li>
    <li style="width:145px">VARNO STORY</li>
    <li style="width:124px">OUR WORK</li>
    <li style="width:142px">CONTACT US</li>
    <li style="width:132px">ELECTRICAL</li>
    <li style="width:164px">LED LIGHTING</li>
    <li style="width:112px">SOLAR POWER</li>
  </ul>
</nav>

<section class="hero abs">
  <div class="hero-photo" role="img" aria-label="Close-up of hands holding a glowing LED downlight in warm orange and violet light"></div>
  <h1 class="hero-title">Varno Electrical</h1>
  <p class="hero-sub">AUSTRALIA'S LARGEST FULLY INTEGRATED ELECTRICAL &amp; ENERGY SOLUTIONS PROVIDER</p>
  <div class="hero-arrow" style="left:28px"><svg width="20" height="20" viewBox="0 0 20 20"><path d="M13 3 L6 10 L13 17" stroke="#fff" stroke-width="3" fill="none"/></svg></div>
  <div class="hero-arrow" style="left:1122px"><svg width="20" height="20" viewBox="0 0 20 20"><path d="M7 3 L14 10 L7 17" stroke="#fff" stroke-width="3" fill="none"/></svg></div>
</section>

<section class="about abs">
  <h2 class="section-title">ABOUT <em>VARNO STORY</em></h2>
  <div class="about-text">
    <p>Electrical and Energy Solutions are at the forefront of our company. Varno Electrical has a long history in Electrical, LED Lighting and Solar Power and just like the Cougar, we will strive to be fierce &amp; agile in an expectations and develop stronger links with all our business partners &amp; community.</p>
    <p>Varno Electrical is an expert Electrical Company providing services to all Residential and Commercial customers. With over 10 years of experience, Varno Electrical has developed a highly-experienced team of professionals that ensure all our customer expectations are exceeded. Our team comprise of over 70 who provide expert advice and quality of installation at an affordable price.</p>
  </div>
  <div class="btn-red">READ MORE INFO</div>
  <svg class="about-photo" width="560" height="330" viewBox="0 0 560 330" role="img" aria-label="Commercial storefront with red and white facade under a pink evening sky">
    <defs>
      <linearGradient id="storeSky" x1="0" y1="0" x2="0" y2="1">
        <stop offset="0" stop-color="#d9c8dc"/><stop offset="0.45" stop-color="#e9d3e0"/>
        <stop offset="0.5" stop-color="#c92a3a"/><stop offset="1" stop-color="#4a4d55"/>
      </linearGradient>
    </defs>
    <polygon points="110,0 560,0 560,330 0,330" fill="url(#storeSky)"/>
  </svg>
</section>

<section class="services abs">
  <svg class="abs" style="left:0;top:0" width="1200" height="70" viewBox="0 0 1200 70" aria-hidden="true">
    <polygon points="0,0 110,14 0,60" fill="#222326"/>
    <polygon points="1200,0 1090,14 1200,60" fill="#222326"/>
  </svg>
  <h2 class="section-title">OUR SERVICES</h2>
  <p class="services-intro">Varno Electrical was formed to be an expert Electricity Contracting Company providing services to all Residential</p>
  <div class="service" style="left:86px">
    <div class="service-photo" role="img" aria-label="Electrician testing a switchboard with a multimeter" style="background:linear-gradient(135deg,#c8d4dc,#7e93a6 50%,#d7dde2)"></div>
    <div class="service-name">ELECTRICAL</div>
  </div>
  <div class="service" style="left:437px">
    <div class="service-photo" role="img" aria-label="Row of glowing LED light bulbs" style="background:radial-gradient(circle at 50% 55%,#f7d48a,#b5701f 45%,#3a220c)"></div>
    <div class="service-name">LED LIGHTING</div>
  </div>
  <div class="service" style="left:788px">
    <div class="service-photo" role="img" aria-label="Solar panel array on green grass under a blue sky" style="background:linear-gradient(180deg,#6fa6e6 0%,#b9d5ef 35%,#3b4656 50%,#5b6675 78%,#5c9a2e 85%,#4b8a25 100%)"></div>
    <div class="service-name">SOLAR POWER</div>
  </div>
</section>

<section class="why abs">
  <h2 class="section-title center-title" style="top:40px">WHY <em>CHOOSE US?</em></h2>
  <p class="center-sub" style="top:84px">Electrical and Energy Solutions are at the forefront of our company. Varno Electrical has a long history in Electrical</p>

  <div class="feature red" style="left:91px">
    <div class="feature-icon"><div>
      <svg width="56" height="56" viewBox="0 0 56 56"><circle cx="28" cy="28" r="17" fill="none" stroke="#fff" stroke-width="7" stroke-dasharray="6 4"/><circle cx="28" cy="28" r="9" fill="#fff"/></svg>
    </div></div>
    <h3>Professional Service</h3>
    <p>When you hire a Varno Electrical you will get a professional and well that skilled and ready to do the job.</p>
  </div>
  <div class="feature dark" style="left:350px">
    <div class="feature-icon"><div>
      <svg width="56" height="56" viewBox="0 0 56 56"><circle cx="28" cy="22" r="15" fill="#fff"/><polygon points="28,13 31,20 38,20 32,24 34,31 28,27 22,31 24,24 18,20 25,20" fill="#2b2b2b"/><polygon points="18,34 14,50 22,46 26,52 28,38" fill="#fff"/><polygon points="38,34 42,50 34,46 30,52 28,38" fill="#fff"/></svg>
    </div></div>
    <h3>5 Year Guarantee</h3>
    <p>When you hire a Varno Electrical you will get a professional and well that skilled and ready to do the job.</p>
  </div>
  <div class="feature red" style="left:610px">
    <div class="feature-icon"><div>
      <svg width="56" height="56" viewBox="0 0 56 56"><path d="M20 10 L36 10 L31 18 Q48 28 44 44 Q42 52 28 52 Q14 52 12 44 Q8 28 25 18 Z" fill="#fff"/><text x="28" y="45" text-anchor="middle" font-family="Roboto,sans-serif" font-weight="700" font-size="20" fill="#ec1f27">$</text></svg>
    </div></div>
    <h3>Value for Money</h3>
    <p>When you hire a Varno Electrical you will get a professional and well that skilled and ready to do the job.</p>
  </div>
  <div class="feature dark" style="left:869px">
    <div class="feature-icon"><div>
      <svg width="56" height="56" viewBox="0 0 56 56"><circle cx="28" cy="30" r="16" fill="none" stroke="#fff" stroke-width="3"/><ellipse cx="28" cy="30" rx="7" ry="16" fill="none" stroke="#fff" stroke-width="2"/><line x1="12" y1="30" x2="44" y2="30" stroke="#fff" stroke-width="2"/><path d="M36 6 Q46 14 40 22 Q44 14 36 6" fill="#fff"/></svg>
    </div></div>
    <h3>Environmentally</h3>
    <p>When you hire a Varno Electrical you will get a professional and well that skilled and ready to do the job.</p>
  </div>
</section>

<section class="clients abs">
  <h2 class="section-title center-title" style="top:22px">OUR <em>SATISFIED CLIENTS</em></h2>
  <p class="center-sub" style="top:66px">Electrical and Energy Solutions are at the forefront of our company. Varno Electrical has a long history in Electrical</p>
  <div class="client" style="left:104px">Brightmere</div>
  <div class="client" style="left:308px"><i></i>Quellbrook Supply</div>
  <div class="client" style="left:516px">Harlowe Plumbing</div>
  <div class="client" style="left:718px"><i></i>Tansy Grill</div>
  <div class="client" style="left:922px">Pellworth Signs</div>
</section>

<footer class="site-footer abs">
  <div class="foot-brand">
    <div class="brand-name">VARNO</div>
    <div class="brand-tag">Spark <span style="color:var(--red)">Every</span> Day</div>
  </div>
  <div class="socials"><span></span><span></span><span></span><span></span><span></span></div>

  <div class="foot-head" style="left:382px">GET IN TOUCH</div>
  <div class="field" style="left:384px;top:81px;width:131px;height:35px">Name :</div>
  <div class="field" style="left:522px;top:81px;width:132px;height:35px">Phone :</div>
  <div class="field" style="left:384px;top:124px;width:270px;height:62px">Message :</div>
  <div class="submit">SUBMIT</div>

  <div class="foot-head" style="left:718px">CONTACT US</div>
  <div class="contact-block">
    <div>Varno Electrical<br>24/88 Larkmoor Rd Ashvale<br>Vic 3190</div>
    <div class="contact-row">
      <svg width="14" height="14" viewBox="0 0 14 14"><path d="M3 1 L5 1 L6 4 L4.5 5.5 Q6 8.5 8.5 9.5 L10 8 L13 9 L13 11 Q12 13 10 13 Q2 11 1 3 Q1 1 3 1Z" fill="#fff"/></svg>
      <span>Phone : 137261</span>
    </div>
    <div class="contact-row email">
      <svg width="14" height="12" viewBox="0 0 14 12"><rect x="1" y="1" width="12" height="10" fill="none" stroke="#fff" stroke-width="1.4"/><path d="M1 1 L7 7 L13 1" fill="none" stroke="#fff" stroke-width="1.4"/></svg>
      <span>Email : service@varnoelectrical-example.com.au</span>
    </div>
  </div>

  <div class="foot-head" style="left:998px">QUICK LINKS</div>
  <ul class="quick-links">
    <li>Home</li><li>Varno Story</li><li>Our Work</li><li>Contact Us</li><li>Career</li>
  </ul>

  <div class="foot-rule"></div>
  <p class="copyright">© Copyright 2017 Varno Electrical. All Rights Reserved</p>
</footer>

</body>
</html>
```